Brin U's Jar Lable for kids Christmas gifts

Looking to get a wrap around label made for a quart canning jar. I would like it to have my kids head on it also. I was thinking in a silhouette form on both ends of the wrap( added a quick sketch up). We will be canning Pickles and giving them away as gifts this year. Also might be selling a few at a frames market. The brand name is " Brin U's" ( at the moment) So if you could think of a cool logo around that would be awesome also. I am an Orange and Black fan but I am up for suggestions also. Do you think this might be something you could help me with?

The second attached graphic is what I would like my kids faces to look similer to. Art wise. The sketch is of what the ends of the labels need to look like. Not a full face but a half of each of there faces on both ends of the lable.

Colors
f78f20
000000
757575

Requirements
Nice to have
• antique lable feel

```html
<!DOCTYPE html>
<html lang="en">
<head>
<meta charset="utf-8">
<title>Brin U's Jar Label</title>
<link href="https://fonts.googleapis.com/css2?family=Oswald:wght@500;700&display=swap" rel="stylesheet">
<style>
  :root {
    --orange: #f78f20;
    --black: #000000;
    --grey: #757575;
    --backdrop: #e4e6e8;
    --white: #ffffff;
  }
  * { margin: 0; padding: 0; box-sizing: border-box; }
  html, body { width: 1200px; height: 1200px; overflow: hidden; }
  body {
    background: var(--backdrop);
    font-family: "Oswald", sans-serif;
    position: relative;
  }
  .label {
    position: absolute;
    left: 20px; top: 310px;
    width: 1160px; height: 581px;
    background: var(--black);
    overflow: hidden;
  }
  .kids-photo {
    position: absolute;
    border: 6px solid var(--white);
    border-bottom: none;
    border-radius: 60px 60px 0 0;
  }
  .kids-photo--left {
    left: 28px; top: 18px; width: 246px; height: 563px;
    background: linear-gradient(180deg, #6b4a3a 0%, #d8322f 30%, #e0403a 55%, #2d3142 78%, #3a3f55 100%);
  }
  .kids-photo--right {
    left: 864px; top: 186px; width: 279px; height: 395px;
    background: linear-gradient(180deg, #4a3328 0%, #8a5a44 30%, #f2b3a8 60%, #e87a86 100%);
  }
  .text-columns {
    position: absolute;
    left: 323px; top: 78px;
    height: 431px;
    writing-mode: vertical-rl;
    color: var(--orange);
    font-weight: 500;
    font-size: 24px;
    line-height: 29px;
    letter-spacing: 0.5px;
    white-space: nowrap;
  }
  .brand-frame {
    position: absolute;
    left: 582px; top: 61px; width: 304px; height: 185px;
    border: 2px dashed var(--white);
    border-radius: 8px;
  }
  .brand-frame__inner {
    position: absolute;
    inset: 15px;
    border: 2px dashed var(--white);
    border-radius: 6px;
    display: flex; align-items: center; justify-content: center;
  }
  .brand-name {
    color: var(--white);
    font-weight: 700;
    font-size: 62px;
    line-height: 1;
  }
  .text-block {
    position: absolute;
    left: 630px; top: 335px;
    color: var(--orange);
    font-weight: 500;
    font-size: 24px;
    line-height: 29px;
    letter-spacing: 0.5px;
    white-space: nowrap;
  }
</style>
</head>
<body>
  <main class="label">
    <div class="kids-photo kids-photo--left" role="img" aria-label="Cut-out photo of a smiling boy in a red tank top making a peace sign"></div>

    <div class="text-columns">
      <p>YOUR TEXT YOUR TEXT YOUR TEXT YOUR TEXT</p>
      <p>YOUR TEXT YOUR TEXT YOUR TEXT YOUR TEXT</p>
      <p>YOUR TEXT YOUR TEXT YOUR TEXT YOUR TEXT</p>
      <p>YOUR TEXT YOUR TEXT YOUR TEXT YOUR TEXT</p>
      <p>YOUR TEXT YOUR TEXT YOUR TEXT YOUR TEXT</p>
      <p>YOUR TEXT YOUR TEXT YOUR TEXT YOUR TEXT</p>
    </div>

    <div class="brand-frame">
      <div class="brand-frame__inner">
        <span class="brand-name">Brin U's</span>
      </div>
    </div>

    <div class="text-block">
      <p>YOUR TEXT YOUR TEXT</p>
      <p>YOUR TEXT YOUR TEXT</p>
      <p>YOUR TEXT YOUR TEXT</p>
      <p>YOUR TEXT YOUR TEXT</p>
      <p>YOUR TEXT YOUR TEXT</p>
      <p>YOUR TEXT YOUR TEXT</p>
    </div>

    <div class="kids-photo kids-photo--right" role="img" aria-label="Cut-out photo of a laughing curly-haired girl in a pink top with a boy behind her"></div>
  </main>
</body>
</html>
```